Veldmark Supplies Business Card

Professional business card that stand out to our potential customers. Front and back with clean modern design

Industry/Entity Type

Oil and gas

Contact Information for Business Card

Name, address, website , office phone and cell number

Requirements
Must have
• Editable files for each employee

```html
<!DOCTYPE html>
<html lang="en">
<head>
<meta charset="utf-8">
<title>Veldmark Supplies – Business Card</title>
<link href="https://fonts.googleapis.com/css2?family=Roboto:wght@400;500;700&display=swap" rel="stylesheet">
<style>
  :root {
    --backdrop: #2b2b2d;
    --card-front: #1c1c1e;
    --card-back: #222225;
    --gloss: #7a7a7e;
    --brand-red: #e8202f;
    --brand-blue: #2ba6d6;
    --text-light: #e6e6e8;
    --text-muted: #c9c9cc;
    --faint-mark: rgba(200, 40, 50, 0.16);
  }
  * { margin: 0; padding: 0; box-sizing: border-box; }
  html, body { width: 1200px; height: 852px; overflow: hidden; }
  body {
    background: var(--backdrop);
    font-family: "Roboto", Arial, sans-serif;
    position: relative;
  }
  .card {
    position: absolute;
    top: 278px;
    width: 520px;
    height: 297px;
    border-radius: 18px;
    overflow: hidden;
  }
  .card--front { left: 60px; background: var(--card-front); }
  .card--back { left: 620px; background: var(--card-back); }

  /* Front */
  .front-mark {
    position: absolute;
    left: 0; right: 0; top: 120px;
    display: flex;
    align-items: center;
    justify-content: center;
    gap: 12px;
  }
  .front-mark__square {
    width: 30px; height: 30px;
    background: var(--gloss);
  }
  .front-mark__name {
    color: var(--gloss);
    font-weight: 700;
    font-size: 30px;
    letter-spacing: 2px;
    text-transform: uppercase;
  }

  /* Back */
  .back-decoration {
    position: absolute;
    right: -40px; top: 10px;
    width: 280px; height: 280px;
    border-radius: 50%;
    background: var(--faint-mark);
  }
  .back-brand {
    position: absolute;
    left: 30px; top: 30px;
    display: flex;
    align-items: center;
    gap: 10px;
  }
  .back-brand__square {
    width: 34px; height: 34px;
    background: var(--brand-red);
  }
  .back-brand__name {
    color: var(--brand-red);
    font-weight: 700;
    font-size: 20px;
    letter-spacing: 1px;
    text-transform: uppercase;
    line-height: 1;
  }
  .contact {
    position: absolute;
    left: 30px; top: 98px;
  }
  .contact__name {
    color: var(--brand-blue);
    font-weight: 500;
    font-size: 22px;
  }
  .contact__role {
    color: var(--text-muted);
    font-size: 13px;
    margin-top: 2px;
  }
  .contact__address {
    color: var(--text-light);
    font-size: 13px;
    line-height: 1.45;
    margin-top: 14px;
  }
  .contact__list {
    list-style: none;
    margin-top: 10px;
  }
  .contact__item {
    display: flex;
    align-items: center;
    gap: 8px;
    color: var(--text-light);
    font-size: 13px;
    line-height: 1.55;
  }
  .contact__icon { width: 12px; height: 12px; fill: var(--brand-red); flex: none; }
</style>
</head>
<body>

<section class="card card--front" aria-label="Card front">
  <div class="front-mark">
    <span class="front-mark__square"></span>
    <span class="front-mark__name">Veldmark Supplies</span>
  </div>
</section>

<section class="card card--back" aria-label="Card back">
  <div class="back-decoration" role="img" aria-label="Faint brand decoration"></div>

  <div class="back-brand">
    <span class="back-brand__square"></span>
    <span class="back-brand__name">Veldmark Supplies</span>
  </div>

  <div class="contact">
    <h1 class="contact__name">Dana Kessler</h1>
    <p class="contact__role">Managing Director</p>
    <p class="contact__address">415 Marlow Ave Suite 3<br>Hollis, Tx 79021</p>
    <ul class="contact__list">
      <li class="contact__item">
        <svg class="contact__icon" viewBox="0 0 24 24"><path d="M6.6 10.8a15 15 0 0 0 6.6 6.6l2.2-2.2a1 1 0 0 1 1-.25 11.4 11.4 0 0 0 3.6.57 1 1 0 0 1 1 1V20a1 1 0 0 1-1 1A17 17 0 0 1 3 4a1 1 0 0 1 1-1h3.5a1 1 0 0 1 1 1c0 1.25.2 2.45.57 3.57a1 1 0 0 1-.25 1z"/></svg>
        (555)014-2290
      </li>
      <li class="contact__item">
        <svg class="contact__icon" viewBox="0 0 24 24"><path d="M2 5h20v14H2z" fill="none"/><path d="M2 5h20v14H2V5zm2 2v.5l8 5 8-5V7H4z"/></svg>
        sales@veldmarksupplies.com
      </li>
      <li class="contact__item">
        <svg class="contact__icon" viewBox="0 0 24 24"><circle cx="12" cy="12" r="10"/></svg>
        www.veldmarksupplies.com
      </li>
    </ul>
  </div>
</section>

</body>
</html>
```